3 Page Design for Ninth Bay Capital

We want a Home Page, About Page, and Products & Services Page for Ninth Bay Capital. Please refer to the attached docs for more info.
If done in Figma, would like Figma files that can easily be ported to Wordpress.

```html
<!DOCTYPE html>
<html lang="en">
<head>
<meta charset="UTF-8">
<title>Ninth Bay Capital — Home</title>
<link href="https://fonts.googleapis.com/css2?family=Archivo:wght@700;800&family=Kumbh+Sans:wght@400;500;600;700&display=swap" rel="stylesheet">
<style>
:root{
  --red:#9b1b30;
  --brown:#8b6a48;
  --beige:#e8dbc6;
  --dark:#2e2c2c;
  --ink:#2b2b2b;
  --muted:#7d7d7d;
  --nav:#5b4e86;
  --white:#ffffff;
}
*{box-sizing:border-box;margin:0;padding:0}
html,body{width:1200px;height:3927px;overflow:hidden;background:var(--white)}
body{font-family:"Kumbh Sans",sans-serif;color:var(--ink)}
.page{position:relative;width:1200px;height:3927px;overflow:hidden}
.abs{position:absolute}
.btn{position:absolute;display:flex;align-items:center;justify-content:center;background:var(--red);color:var(--white);font-size:15px;font-weight:500;border-radius:3px;text-decoration:none}
.h2{font-family:"Archivo",sans-serif;font-weight:700;color:var(--ink);letter-spacing:.5px}
.rule{position:absolute;height:3px;width:58px;background:var(--red);border-radius:2px}
.sub{color:var(--brown);font-weight:600}
.copy{color:var(--muted);font-size:14px;line-height:24px}
.photo{position:absolute}

/* header */
.header{position:absolute;left:0;top:0;width:1200px;height:102px;background:var(--white);box-shadow:0 1px 6px rgba(0,0,0,.06);z-index:5}
.brand{position:absolute;left:111px;top:34px;display:flex;align-items:center;gap:10px;font-weight:700;font-size:19px;color:var(--ink)}
.brand-dot{width:26px;height:26px;border-radius:50%;background:var(--brown)}
.nav a{position:absolute;top:42px;font-size:15px;color:#444;text-decoration:none;transform:translateX(-50%)}
.nav .active{color:var(--nav)}
.nav .active::after{content:"";position:absolute;left:0;right:0;bottom:-6px;height:2px;background:var(--nav)}

/* hero */
.hero-bg{left:0;top:102px;width:1200px;height:690px;background:linear-gradient(100deg,#f2f1ee 0%,#e6e4df 45%,#c9b9a6 70%,#a69682 100%)}
.hero-crowd{left:0;top:520px;width:1200px;height:170px;background:linear-gradient(180deg,rgba(120,100,80,0) 0%,rgba(110,90,72,.55) 100%)}
.hero-title{left:111px;top:190px;font-size:60px;line-height:64px}
.hero-sub{left:111px;top:262px;font-family:"Archivo",sans-serif;font-weight:700;font-size:44px;color:var(--brown)}
.hero-text{left:111px;top:336px;width:560px;font-size:20px;line-height:28px;color:#7a7a7a}
.dots{position:absolute;display:flex;gap:9px}
.dots span{width:24px;height:8px;border-radius:4px;background:var(--white)}

/* about */
.about-title{left:647px;top:976px;font-size:40px}
.about-sub{left:645px;top:1066px;font-size:22px}
.about-copy{left:645px;top:1122px;width:443px;text-align:justify}

/* provide */
.center{left:0;width:1200px;text-align:center}
.card-img{position:absolute;top:1853px;width:306px;height:245px;border-radius:12px}
.card-title{position:absolute;top:2112px;width:306px;text-align:center;font-size:23px;font-weight:600;color:var(--ink)}
.card-text{position:absolute;top:2152px;width:306px;text-align:center;font-size:14.5px;line-height:24px;color:#444}

/* cta */
.cta{left:111px;top:3018px;width:976px;height:459px;background:var(--beige);border-radius:34px 0 34px 0}
.cta-img{left:131px;top:3039px;width:342px;height:418px;border-radius:20px 0 20px 0;background:linear-gradient(160deg,#d8d3c8 0%,#b9ad9c 55%,#8c7d6c 100%)}

/* footer */
.fbrand{left:114px;top:3640px;font-size:30px;font-weight:700;color:var(--white);display:flex;align-items:center;gap:12px}
.fbrand i{width:34px;height:34px;border-radius:50%;background:var(--white);display:block}
.social{position:absolute;top:3776px;width:30px;height:30px;border-radius:50%;background:#f2f2f2}
.social.first{background:#6a5ea8;border-radius:4px}
.fhead{position:absolute;top:3586px;font-size:21px;font-weight:600;color:var(--white)}
.flink{position:absolute;font-size:14.5px;color:var(--white);display:flex;align-items:center;gap:14px}
.divider{left:111px;top:3883px;width:976px;height:1px;background:#4a4747}
.copyright{left:0;top:3898px;width:1200px;text-align:center;font-size:13px;color:var(--white)}
</style>
</head>
<body>
<div class="page">

  <!-- hero -->
  <div class="abs hero-bg" role="img" aria-label="Photo of a confident woman speaking to a seated audience in a bright room"></div>
  <div class="abs hero-crowd"></div>
  <h1 class="abs h2 hero-title">YOUR NEXT CHAPTER</h1>
  <div class="abs hero-sub">STARTS WITH INTENTION.</div>
  <p class="abs hero-text">We help high-performers move beyond the spotlight with a modern system of wealth, strategy, and support — designed for life after the game.</p>
  <a class="btn" style="left:111px;top:447px;width:215px;height:39px">Build Your Next Chapter</a>

  <svg class="abs" style="left:0;top:600px" width="1200" height="200" viewBox="0 0 1200 200">
    <path d="M0,48 Q560,220 1200,48 L1200,200 L0,200 Z" fill="#fff"/>
    <path d="M60,70 Q600,250 1200,40 L1200,52 Q620,225 60,70 Z" fill="#8b6a48"/>
  </svg>
  <div class="dots" style="left:555px;top:691px"><span></span><span></span><span></span></div>

  <!-- header -->
  <header class="header">
    <div class="brand"><span class="brand-dot"></span>Ninth Bay Capital</div>
    <nav class="nav">
      <a class="active" style="left:514px">Home</a>
      <a style="left:632px">About Us</a>
      <a style="left:796px">Products &amp; Services</a>
    </nav>
    <a class="btn" style="left:938px;top:32px;width:149px;height:38px">Start Your Plan</a>
  </header>

  <!-- about -->
  <div class="photo" style="left:-60px;top:862px;width:517px;height:529px;border-radius:50%;background:linear-gradient(150deg,#9fb7bd 0%,#7d8f88 45%,#4f5c5a 100%)" role="img" aria-label="Photo of three friends jogging together outdoors"></div>
  <div class="photo" style="left:221px;top:1171px;width:294px;height:285px;border-radius:50%;background:linear-gradient(160deg,#dfe6ea 0%,#b3a58f 55%,#6d5a48 100%);border:4px solid #fff" role="img" aria-label="Photo of a speaker presenting to a seated group"></div>
  <h2 class="abs h2 about-title">ABOUT US</h2>
  <div class="rule" style="left:647px;top:1032px"></div>
  <div class="abs sub about-sub">Built for the Chapter After the Spotlight</div>
  <div class="abs copy about-copy">
    <p>Ninth Bay Capital exists to guide athletes and entrepreneurs through one of the most important transitions of their lives — the move from performance to long-term stability, identity, and generational success.</p>
    <p style="margin-top:24px">We understand the discipline, pressure, and ambition that come with high-performance careers. But we also understand what happens when the season ends, the game shifts, or the business needs stronger structure.</p>
  </div>
  <a class="btn" style="left:647px;top:1369px;width:149px;height:38px">Read More</a>

  <!-- provide -->
  <svg class="abs" style="left:0;top:1560px" width="1200" height="900" viewBox="0 0 1200 900">
    <path d="M0,130 Q600,-60 1200,130 L1200,750 Q600,950 0,750 Z" fill="#e8dbc6"/>
    <path d="M40,118 Q600,-70 1160,120 L1150,124 Q600,-40 40,118 Z" fill="#8b6a48"/>
    <path d="M30,762 Q600,980 1190,750 L1180,760 Q600,950 30,762 Z" fill="#8b6a48"/>
  </svg>
  <h2 class="abs h2 center" style="top:1694px;font-size:40px">WHAT WE PROVIDE</h2>
  <div class="rule" style="left:571px;top:1752px"></div>
  <div class="abs sub center" style="top:1774px;font-size:22px">Structured support for long-term success</div>

  <div class="card-img" style="left:111px;background:linear-gradient(160deg,#cfc9bf,#8d7f70)" role="img" aria-label="Photo of a group sitting on a wooden floor in conversation"></div>
  <div class="card-title" style="left:111px">Wealth Planning Systems</div>
  <div class="card-text" style="left:111px">Lorem ipsum dolor sit amet, consectetur adipiscing elit, sed do eiusmod tempor incididunt ut labore et dolore aliqua.</div>
  <a class="btn" style="left:178px;top:2243px;width:174px;height:38px">Discover More</a>

  <div class="card-img" style="left:445px;background:linear-gradient(160deg,#c9a47a,#6b5443)" role="img" aria-label="Photo of people seated at a workshop listening"></div>
  <div class="card-title" style="left:445px">Business &amp; Transition</div>
  <div class="card-text" style="left:445px">Lorem ipsum dolor sit amet, consectetur adipiscing elit, sed do eiusmod tempor incididunt ut labore et dolore aliqua.</div>
  <a class="btn" style="left:512px;top:2243px;width:174px;height:38px">Discover More</a>

  <div class="card-img" style="left:779px;background:linear-gradient(160deg,#c7c7c4,#4f4c4a)" role="img" aria-label="Aerial photo of professionals mingling in an office lobby"></div>
  <div class="card-title" style="left:779px">Performance Systems</div>
  <div class="card-text" style="left:779px">Lorem ipsum dolor sit amet, consectetur adipiscing elit, sed do eiusmod tempor incididunt ut labore et dolore aliqua.</div>
  <a class="btn" style="left:846px;top:2243px;width:174px;height:38px">Discover More</a>

  <div class="dots" style="left:555px;top:2353px">
    <span style="background:var(--red)"></span><span style="background:var(--brown)"></span><span style="background:var(--brown)"></span>
  </div>

  <!-- mission -->
  <h2 class="abs h2 center" style="top:2552px;font-size:40px">OUR MISSION</h2>
  <div class="rule" style="left:571px;top:2608px"></div>
  <div class="abs sub center" style="top:2633px;font-size:22px">Creating clarity and structure for your next chapter.</div>
  <div class="abs copy" style="left:230px;top:2681px;width:740px;text-align:center">
    <p>Our mission is to guide athletes and entrepreneurs into long-term success through structure, clarity, and refined strategy. We merge the discipline of sports, the precision of business, and the power of automated systems to create a modern approach to wealth and wellness.</p>
    <p style="margin-top:24px">Our work ensures that high-performers not only excel in their prime — but remain confident, prepared, and empowered long after the moment fades.</p>
  </div>
  <a class="btn" style="left:526px;top:2861px;width:150px;height:38px">Read More</a>

  <!-- footer band -->
  <svg class="abs" style="left:0;top:3300px" width="1200" height="627" viewBox="0 0 1200 627">
    <path d="M0,90 Q600,-70 1200,90 L1200,627 L0,627 Z" fill="#2e2c2c"/>
    <path d="M0,70 Q600,-95 1200,70 L1200,90 Q600,-70 0,90 Z" fill="#8b6a48"/>
  </svg>

  <!-- cta -->
  <div class="abs cta"></div>
  <div class="abs cta-img" role="img" aria-label="Photo of a yoga instructor guiding a student in a stretch"></div>
  <h2 class="abs h2" style="left:551px;top:3084px;font-size:40px;line-height:44px">READY TO BUILD YOUR<br>NEXT CHAPTER?</h2>
  <div class="rule" style="left:551px;top:3186px"></div>
  <div class="abs sub" style="left:550px;top:3212px;width:500px;font-size:21px;line-height:24px">Structured support for long-term clarity and success.</div>
  <p class="abs copy" style="left:550px;top:3284px;width:443px;text-align:justify">Build with intention. Our system helps you create disciplined momentum and a clear path forward—on and off the field.</p>
  <a class="btn" style="left:551px;top:3363px;width:149px;height:38px">Start Your Plan</a>

  <!-- footer -->
  <div class="abs fbrand"><i></i>Ninth Bay<br>Capital</div>
  <div class="social first" style="left:114px"></div>
  <div class="social" style="left:164px"></div>
  <div class="social" style="left:211px"></div>
  <div class="social" style="left:258px"></div>

  <div class="fhead" style="left:407px">Main Links</div>
  <div class="flink" style="left:407px;top:3642px">Home</div>
  <div class="flink" style="left:407px;top:3694px">About</div>
  <div class="flink" style="left:407px;top:3744px">Products &amp; Services</div>

  <div class="fhead" style="left:644px">Contact Us</div>
  <div class="flink" style="left:644px;top:3640px">
    <svg width="20" height="22" viewBox="0 0 20 22" fill="none" stroke="#fff" stroke-width="1.6"><path d="M10 21s7-7 7-12A7 7 0 0 0 3 9c0 5 7 12 7 12z"/><circle cx="10" cy="9" r="2.5"/></svg>12 Harbor Row, Suite 4</div>
  <div class="flink" style="left:644px;top:3694px">
    <svg width="20" height="20" viewBox="0 0 24 24" fill="none" stroke="#fff" stroke-width="1.6"><path d="M5 3h4l2 5-2.5 1.5a11 11 0 0 0 6 6L16 13l5 2v4a2 2 0 0 1-2 2A17 17 0 0 1 3 5a2 2 0 0 1 2-2z"/></svg>+1 555 014 2290</div>
  <div class="flink" style="left:644px;top:3744px">
    <svg width="20" height="16" viewBox="0 0 20 16" fill="none" stroke="#fff" stroke-width="1.6"><rect x="1" y="1" width="18" height="14" rx="2"/><path d="M1 2l9 7 9-7"/></svg>info@ninthbaycapital.com</div>

  <div class="fhead" style="left:956px">Other Links</div>
  <div class="flink" style="left:956px;top:3642px">Cookies Policy</div>
  <div class="flink" style="left:956px;top:3694px">Terms &amp; Conditions</div>
  <div class="flink" style="left:956px;top:3744px">Privacy Policy</div>

  <div class="abs divider"></div>
  <div class="abs copyright">Copyright © 2025 Ninth Bay Capital. All rights reserved.</div>
</div>
</body>
</html>
```